design a construction company business card

Design business card around our logo. Card must have all the typical info: name, title, address, phone, email, business name, etc. Somewhere on the card I would like to see our motto "Built on integrity... Inspired by commitment." Consider adding a splash of bright orange to the card to complement the blues and silvers/grays in the logo. We are open to metallic inks, textures, etc. We would like to see options on both light and dark backgrounds. The font in the logo is Euro Technic Extended Regular.

```html
<!DOCTYPE html>
<html lang="en">
<head>
<meta charset="utf-8">
<title>Harlow Contracting – Business Card</title>
<link rel="stylesheet" href="https://fonts.googleapis.com/css2?family=Ubuntu:wght@400;500&display=swap">
<style>
  :root {
    --page: #ffffff;
    --night: #000000;
    --sky-dark: #333333;
    --sky-orange: #ff6600;
    --accent: #ff6a00;
    --brand-blue: #3a66c4;
    --ink-light: #ffffff;
    --trim: #9a9a9a;
    --guide: #666666;
  }
  * { margin: 0; padding: 0; box-sizing: border-box; }
  html, body {
    width: 1200px; height: 866px; overflow: hidden;
    background: var(--page);
    font-family: "Ubuntu", sans-serif;
  }
  .sheet { position: relative; width: 1200px; height: 866px; }

  .card {
    position: absolute; top: 96px;
    width: 440px; height: 674px;
    background: var(--night);
    overflow: hidden;
    text-align: center;
  }
  .card--front { left: 100px; }
  .card--back { left: 661px; }

  .card__skyline {
    position: absolute; left: 0; top: 0; width: 100%;
  }
  .card--front .card__skyline {
    height: 300px;
    background: linear-gradient(180deg, var(--sky-dark) 0%, var(--sky-dark) 45%, var(--night) 100%);
  }
  .card--back .card__skyline {
    height: 250px;
    background: linear-gradient(180deg, var(--sky-orange) 0%, var(--sky-orange) 40%, var(--night) 100%);
  }

  .card__safe-area {
    position: absolute; left: 34px; top: 34px; right: 34px; bottom: 34px;
    border: 1px dotted var(--guide);
    pointer-events: none;
  }

  .brand-name {
    position: absolute; left: 0; right: 0;
    color: var(--brand-blue);
    font-weight: 500;
    font-size: 24px;
    letter-spacing: 2px;
    line-height: 1;
  }
  .card--front .brand-name { top: 306px; }
  .card--back .brand-name { top: 256px; }

  .motto {
    position: absolute; left: 0; right: 0; top: 397px;
    color: var(--accent);
    font-size: 26px;
    line-height: 38.5px;
    letter-spacing: 1px;
  }

  .person { position: absolute; left: 0; right: 0; top: 338px; }
  .person__name {
    color: var(--accent);
    font-weight: 500;
    font-size: 32px;
    line-height: 1.2;
    letter-spacing: 0.5px;
  }
  .person__title { color: var(--ink-light); font-size: 14px; margin-top: 3px; }

  .contact, .address {
    position: absolute; left: 0; right: 0;
    color: var(--ink-light);
    font-size: 15.5px;
    line-height: 19.6px;
    font-style: normal;
  }
  .contact { top: 470px; }
  .address { top: 543px; }

  .crop-mark {
    position: absolute; width: 53px; height: 53px;
    border: 1px solid var(--trim);
  }
</style>
</head>
<body>
<main class="sheet">

  <section class="card card--front" aria-label="Card front">
    <div class="card__skyline" role="img" aria-label="City skyline silhouette against a dark grey sky"></div>
    <div class="card__safe-area"></div>
    <p class="brand-name">HARLOW CONTRACTING</p>
    <p class="motto">Built<br>On Integrity<br>Inspired<br>By Commitment</p>
  </section>

  <section class="card card--back" aria-label="Card back">
    <div class="card__skyline" role="img" aria-label="City skyline silhouette against a bright orange sky"></div>
    <div class="card__safe-area"></div>
    <p class="brand-name">HARLOW CONTRACTING</p>
    <div class="person">
      <h1 class="person__name">Dana Whitfield</h1>
      <p class="person__title">Senior Project Manager</p>
    </div>
    <p class="contact">Phone: 555.201.4477<br>Fax: 555.201.4478<br>Email: info@harlowcontracting.com</p>
    <address class="address">Harlow Contracting, Inc.<br>2207 Ridgeline Avenue<br>Dayton, OH 45409</address>
  </section>

  <div class="crop-mark" style="left:82px;top:77px"></div>
  <div class="crop-mark" style="left:506px;top:77px"></div>
  <div class="crop-mark" style="left:82px;top:737px"></div>
  <div class="crop-mark" style="left:506px;top:737px"></div>
  <div class="crop-mark" style="left:642px;top:77px"></div>
  <div class="crop-mark" style="left:1066px;top:77px"></div>
  <div class="crop-mark" style="left:642px;top:737px"></div>
  <div class="crop-mark" style="left:1066px;top:737px"></div>

</main>
</body>
</html>
```